Robotic Physical Therapy office needs a Grand Opening Flyer

We need a Grand Opening flyer design for a robotic physical therapy office named Kinetic Harbor Wellness. We would like it to have a clean, classy, upscale feeling that gives potential clients a V.I.P. feeling. We would like to use the colors black, gray, and yellow (logo will be uploaded).

Event: Thursday, June 1st, 2023 from 12pm-6pm
location: 58274 Pellham Ave, Bloomfield Hills, MI 48519

Industry/Entity Type

Physical therapy

Font styles to use
Script

Colors

Designer to choose colors to be used in the design.

Requirements
Nice to have
• More of a vip feel for the invite

```html
<!DOCTYPE html>
<html lang="en">
<head>
<meta charset="utf-8">
<title>Kinetic Harbor Wellness – Grand Opening</title>
<link rel="stylesheet" href="https://fonts.googleapis.com/css2?family=Montserrat:wght@300;400;600;700&family=Open+Sans:wght@300;400;700&family=Great+Vibes&display=swap">
<style>
  :root {
    --bg-light: #303030;
    --bg-mid: #262626;
    --bg-dark: #161616;
    --facet: #1b1b1b;
    --facet-soft: #3a3a3a;
    --gold-line: #8a6a3a;
    --brand-yellow: #f2d83a;
    --gold: #eaa93c;
    --gold-light: #f6cf5a;
    --orange: #e0892a;
    --silver-hi: #f2f2f4;
    --silver-mid: #a9a9ad;
    --silver-lo: #6d6d72;
    --body-gray: #8b8b8b;
    --address-gray: #8e8e8e;
    --white: #ffffff;
  }
  * { margin: 0; padding: 0; box-sizing: border-box; }
  html, body {
    width: 935px; height: 1200px; overflow: hidden;
    background: var(--bg-dark);
  }
  .flyer {
    position: relative;
    width: 935px; height: 1200px;
    overflow: hidden;
    background: linear-gradient(160deg, var(--bg-mid) 0%, var(--bg-light) 45%, var(--bg-mid) 70%, var(--bg-dark) 100%);
    text-align: center;
  }
  .flyer__facets { position: absolute; inset: 0; width: 935px; height: 1200px; }
  .flyer__content { position: relative; z-index: 1; }

  .brand {
    position: absolute; left: 0; right: 0; top: 104px;
    display: flex; align-items: center; justify-content: center; gap: 14px;
  }
  .brand__dot {
    width: 62px; height: 62px; border-radius: 50%;
    background: var(--brand-yellow);
  }
  .brand__name {
    font-family: "Montserrat", sans-serif; font-weight: 700;
    font-size: 34px; line-height: 1.05; color: var(--brand-yellow);
    text-align: left; text-transform: uppercase;
  }

  .service {
    position: absolute; left: 0; right: 0; top: 352px;
    font-family: "Montserrat", sans-serif; font-weight: 400;
    font-size: 30px; line-height: 38px; letter-spacing: 4px;
    color: var(--gold);
  }

  .headline-grand {
    position: absolute; left: 0; right: 0; top: 430px;
    font-family: "Montserrat", sans-serif; font-weight: 600;
    font-size: 160px; line-height: 170px;
    background: linear-gradient(180deg, var(--silver-hi) 0%, var(--silver-mid) 45%, var(--silver-lo) 60%, var(--silver-hi) 100%);
    -webkit-background-clip: text; background-clip: text;
    color: transparent;
    padding-left: 10px;
  }
  .headline-opening {
    position: absolute; left: 0; right: 0; top: 550px;
    font-family: "Great Vibes", cursive;
    font-size: 112px; line-height: 130px;
    background: linear-gradient(180deg, var(--gold-light) 0%, var(--orange) 100%);
    -webkit-background-clip: text; background-clip: text;
    color: transparent;
    padding-left: 10px;
  }

  .intro {
    position: absolute; left: 0; right: 0; top: 692px;
    font-family: "Open Sans", sans-serif; font-weight: 300;
    font-size: 20px; line-height: 29px; color: var(--body-gray);
  }

  .event-date {
    position: absolute; left: 0; right: 0; top: 826px;
    font-family: "Open Sans", sans-serif; font-weight: 700;
    font-size: 32px; line-height: 46px; letter-spacing: 3px;
    background: linear-gradient(180deg, var(--gold) 0%, var(--gold-light) 100%);
    -webkit-background-clip: text; background-clip: text;
    color: transparent;
  }
  .event-date sup { font-size: 18px; vertical-align: 14px; letter-spacing: 1px; }

  .address {
    position: absolute; left: 0; right: 0; top: 958px;
    font-family: "Open Sans", sans-serif; font-weight: 400;
    font-size: 21px; line-height: 32px; letter-spacing: 7.5px;
    color: var(--address-gray);
  }

  .website {
    position: absolute; left: 314px; top: 1072px;
    width: 307px; height: 46px;
    border: 1.5px solid var(--brand-yellow); border-radius: 23px;
    font-family: "Montserrat", sans-serif; font-weight: 600;
    font-size: 21px; line-height: 43px; color: var(--white);
    letter-spacing: 0.5px;
  }
</style>
</head>
<body>
<main class="flyer">
  <svg class="flyer__facets" viewBox="0 0 935 1200" aria-hidden="true">
    <polygon points="0,0 935,0 935,150 650,460 330,100 0,100" fill="var(--facet)" opacity="0.35"/>
    <polygon points="935,150 935,1200 700,1200 935,900" fill="var(--facet)" opacity="0.55"/>
    <polygon points="0,1200 0,820 420,1200" fill="var(--facet-soft)" opacity="0.25"/>
    <polygon points="560,1200 935,760 935,1200" fill="var(--facet)" opacity="0.5"/>
    <line x1="0" y1="254" x2="216" y2="0" stroke="var(--gold-line)" stroke-width="1.2"/>
    <line x1="935" y1="795" x2="593" y2="1200" stroke="var(--gold-line)" stroke-width="1.2"/>
  </svg>

  <div class="flyer__content">
    <header class="brand">
      <span class="brand__dot"></span>
      <span class="brand__name">Kinetic Harbor<br>Wellness</span>
    </header>

    <p class="service">ROBOTIC PHYSICAL<br>THERAPY</p>

    <h1>
      <span class="headline-grand">GRAND</span>
      <span class="headline-opening">Opening</span>
    </h1>

    <p class="intro">Lorem ipsum dolor sit amet, etera<br>consectetuer adipiscing elit.<br>Aenean commodo ligula eget dolor.</p>

    <p class="event-date">1<sup>st</sup> June,Thursday 2023<br>12PM-6PM</p>

    <p class="address">58274 Pellham Ave, Bloomfield<br>Hills, MI 48519</p>

    <p class="website">www.website.com</p>
  </div>
</main>
</body>
</html>
```